IT Company requires new Business Card design.

Over the years we have had a few different business card designs. We are now due for new cards across the board for all staff. We felt this would be a good time to start fresh with a new design. Our traditional card simply had our details on the front, and a list of services on the back. We don't particularly need the list of services, we have had cards where the only thing on the rear of the card was our logo.
Feel free to be creative, we would like our tag line "Complete IT Management" to appear at some point, doesn't necessarily have to be with the logo.
I have attached samples and drafts of various previous cards we have used over the years.

```html
<!DOCTYPE html>
<html lang="en">
<head>
<meta charset="utf-8">
<title>Harbor Links – Business Card</title>
<link rel="stylesheet" href="https://fonts.googleapis.com/css2?family=PT+Sans:wght@400;700&display=swap">
<style>
  :root {
    --backdrop: #6a3a24;
    --card-dark: #262626;
    --card-mid: #3a3a3a;
    --card-light: #4a4a4a;
    --name-band: #7d8d9c;
    --text-light: #f2f2f2;
    --mark-grey: #b9b9b9;
    --mark-faint: #8a8a8a;
  }
  html, body {
    margin: 0;
    padding: 0;
    width: 1200px;
    height: 992px;
    overflow: hidden;
    background: var(--backdrop);
    font-family: "PT Sans", Arial, sans-serif;
  }
  .canvas {
    position: relative;
    width: 1200px;
    height: 992px;
  }
  .card {
    position: absolute;
    top: 47px;
    width: 500px;
    height: 878px;
    overflow: hidden;
    background:
      repeating-linear-gradient(90deg, rgba(255,255,255,0.015) 0 1px, transparent 1px 3px),
      linear-gradient(180deg, var(--card-mid), var(--card-dark));
    box-shadow: 0 4px 14px rgba(0,0,0,0.45);
  }
  .card--front { left: 84px; }
  .card--back {
    left: 634px;
    background:
      repeating-linear-gradient(90deg, rgba(255,255,255,0.015) 0 1px, transparent 1px 3px),
      radial-gradient(ellipse at 50% 45%, var(--card-light) 0%, var(--card-mid) 35%, var(--card-dark) 80%);
  }

  .name-band {
    position: absolute;
    left: 0;
    top: 50px;
    width: 302px;
    height: 92px;
    background: var(--name-band);
    color: var(--text-light);
    box-sizing: border-box;
    padding: 12px 0 0 36px;
  }
  .name-band__name {
    margin: 0;
    font-size: 27px;
    font-weight: 700;
    letter-spacing: 0.3px;
    line-height: 1.15;
  }
  .name-band__title {
    margin: 4px 0 0;
    font-size: 20px;
    font-weight: 400;
    line-height: 1.1;
  }

  .contact-list {
    position: absolute;
    left: 17px;
    top: 164px;
    margin: 0;
    padding: 0;
    list-style: none;
    color: var(--text-light);
    font-size: 21px;
  }
  .contact-list li {
    display: flex;
    align-items: center;
    height: 43px;
  }
  .contact-list svg {
    width: 20px;
    height: 20px;
    margin-right: 15px;
    fill: var(--text-light);
  }
  .address {
    position: absolute;
    left: 34px;
    top: 408px;
    margin: 0;
    color: var(--text-light);
    font-size: 21px;
  }

  .brand-faint {
    position: absolute;
    left: 40px;
    bottom: 60px;
    margin: 0;
    color: var(--mark-faint);
    font-size: 52px;
    font-weight: 700;
    letter-spacing: 1px;
  }

  .brand-name {
    position: absolute;
    left: 0;
    right: 0;
    top: 388px;
    margin: 0;
    text-align: center;
    color: var(--mark-grey);
    font-size: 60px;
    font-weight: 700;
    letter-spacing: 1px;
  }
  .tagline {
    position: absolute;
    left: 0;
    right: 0;
    top: 818px;
    margin: 0;
    text-align: center;
    color: var(--text-light);
    font-size: 20px;
    letter-spacing: 4.5px;
    text-transform: uppercase;
  }
</style>
</head>
<body>
<main class="canvas">
  <section class="card card--front">
    <div class="name-band">
      <h1 class="name-band__name">MARCUS REID</h1>
      <p class="name-band__title">OPERATION MANAGER</p>
    </div>

    <ul class="contact-list">
      <li>
        <svg viewBox="0 0 20 20" aria-hidden="true"><path d="M5 2l3 4-2 2c1 2 3 4 5 5l2-2 4 3-2 3C9 17 3 11 2 4z"/></svg>
        08 9000 1234
      </li>
      <li>
        <svg viewBox="0 0 20 20" aria-hidden="true"><path d="M6 1h8v18H6zM7.5 3v9h5V3zM8 14h1v1H8zm2 0h1v1h-1zm2 0h1v1h-1zM8 16h1v1H8zm2 0h1v1h-1zm2 0h1v1h-1z" fill-rule="evenodd"/></svg>
        0400 123 456
      </li>
      <li>
        <svg viewBox="0 0 20 20" aria-hidden="true"><path d="M5 3h8l2 2v3H5zM1 9h18v8H1zM5 14h10v3H5z"/></svg>
        08 9000 1235
      </li>
      <li>
        <svg viewBox="0 0 20 20" aria-hidden="true"><path d="M1 6l9-4 9 4v11H1zm2 1l7 5 7-5-7-3z" fill-rule="evenodd"/></svg>
        marcus@harborlinks.com.au
      </li>
      <li>
        <svg viewBox="0 0 20 20" aria-hidden="true"><path d="M10 1a9 9 0 100 18 9 9 0 000-18zm0 2c1 1 2 3 2.3 6H7.7C8 6 9 4 10 3zM3.1 9h2.6c.1-2 .6-4 1.5-5.3A7 7 0 003.1 9zm9.7-5.3c.9 1.3 1.4 3.3 1.5 5.3h2.6a7 7 0 00-4.1-5.3zM3.1 11a7 7 0 004.1 5.3c-.9-1.3-1.4-3.3-1.5-5.3zm4.6 0c.3 3 1.3 5 2.3 6 1-1 2-3 2.3-6zm6.6 0c-.1 2-.6 4-1.5 5.3a7 7 0 004.1-5.3z" fill-rule="evenodd"/></svg>
        www.harborlinks.com.au
      </li>
    </ul>

    <p class="address">Unit 4 12 Sample Way, Bellmont WA 6000</p>

    <p class="brand-faint">HARBOR LINKS</p>
  </section>

  <section class="card card--back">
    <p class="brand-name">HARBOR LINKS</p>
    <p class="tagline">Complete IT Management</p>
  </section>
</main>
</body>
</html>
```